VitaBraid Web Design. Health and Wellness Industry

We are in process of creating next big Cloud based Health Care Management system. We have created 1st draft of Landing Page design. It is missing curb appeal, jazzy feel and engaging modern look.

Need a talented designer to recreate UI/ UX and take it to the next level.
If you are a creative designer, gifted with vision and imagination, I strongly encourage you to participate.

I want the designers to stay focus on the Landing page
Once we select the winner we will provide other subsequent pages
Follow up pages will be similar simple design

Target Market(s)

Individual Users and small business
Age Group 35-75
Individuals involved in "Health and Fitness" activity tracking, managing etc.

Industry/Entity Type

Health And Wellness

Number of Pages Required

5+ page

Colors
f68e4e
34a6d7

Requirements
Must have
• Super Engaging UI/ UX
• Smart and Contemporary look
• Easy to Navigate
• Folder Style menu bar
• Slideshow
• Social Medial Friendly
• Online Shopping
Nice to have
• Start from the enclosed draft Landing Page Idea.
• Feel Free to include additional frame, information section, Icon etc.

```html
<!DOCTYPE html>
<html lang="en">
<head>
<meta charset="utf-8">
<title>VitaBraid — Health Care Management System</title>
<link href="https://fonts.googleapis.com/css2?family=Roboto:wght@300;400;500;700&display=swap" rel="stylesheet">
<style>
:root{
  --orange:#f68e4e;
  --blue:#34a6d7;
  --ink:#333;
  --muted:#777;
  --topbar:#3c3c3c;
  --light:#f1f1f1;
  --line:#e2e2e2;
  --white:#fff;
}
*{box-sizing:border-box;margin:0;padding:0}
html,body{width:1200px;height:2676px;overflow:hidden}
body{font-family:"Roboto",Arial,sans-serif;color:var(--ink);background:var(--white);font-size:14px}
.wrap{width:1100px;margin:0 auto;position:relative}

.topbar{height:32px;background:var(--topbar);color:#ddd;font-size:12px}
.topbar .wrap{display:flex;justify-content:space-between;align-items:center;height:32px}
.topbar nav span{margin-left:18px}

.header{height:128px;background:var(--white)}
.header .wrap{display:flex;justify-content:space-between;align-items:center;height:128px}
.brand{display:flex;align-items:center;gap:12px;font-size:40px;font-weight:500;color:var(--orange)}
.brand i{width:44px;height:44px;border-radius:50%;background:var(--orange);display:block}
.mainnav{display:flex;gap:34px;font-size:14px;font-weight:500}
.mainnav a{color:var(--ink);text-decoration:none}
.mainnav a.active{color:var(--blue)}

.hero{height:608px;position:relative;background:linear-gradient(100deg,#d9e4ec 0%,#eef3f7 45%,#f8fbfd 70%,#e3eef5 100%)}
.hero-photo{position:absolute;inset:0}
.hero-text{position:absolute;left:740px;top:340px}
.hero-text h1{font-size:66px;font-weight:400;color:var(--blue);line-height:1}
.hero-text p{font-size:42px;font-weight:300;color:#333;margin-top:8px}
.hero-arrows{position:absolute;left:1036px;top:572px;display:flex;gap:4px}
.hero-arrows span{width:26px;height:26px;background:#444;display:flex;align-items:center;justify-content:center}

.welcome{height:540px;padding-top:80px;text-align:center}
.welcome h2{font-size:26px;font-weight:500;letter-spacing:1px}
.welcome h2 b{color:var(--orange);font-weight:500}
.welcome .lead{width:1060px;margin:20px auto 0;font-size:13px;line-height:1.7;color:var(--muted)}
.cards{display:flex;gap:16px;justify-content:center;margin-top:36px}
.card{width:252px;height:262px;background:var(--white);border:1px solid var(--line);box-shadow:0 3px 8px rgba(0,0,0,.08);padding:30px 24px 0}
.card .icon{width:70px;height:70px;border-radius:50%;background:var(--orange);margin:0 auto;display:flex;align-items:center;justify-content:center;box-shadow:0 0 0 6px #fde2d1}
.card h3{color:var(--orange);font-size:14px;font-weight:500;margin-top:28px}
.card p{font-size:12px;line-height:1.6;color:var(--muted);margin-top:12px}

.system{height:302px;background:linear-gradient(90deg,#2f2f2f,#4a4a4a 60%,#3a3a3a)}
.system .wrap{display:flex;gap:30px;padding-top:44px}
.system-photo{width:310px;height:214px;background:linear-gradient(135deg,#bcd9ea,#7fb6d6 55%,#e9eef2)}
.system-copy{width:700px}
.system-copy h2{font-size:26px;font-weight:400;color:var(--white)}
.system-copy p{font-size:13px;line-height:1.7;color:#cfcfcf;margin-top:14px}
.btn{display:inline-block;background:var(--orange);color:var(--white);font-size:13px;padding:10px 20px;margin-top:20px;border-radius:2px}

.products{height:470px;padding-top:56px}
.products-head{display:flex;justify-content:space-between;align-items:center}
.products-head h2{font-size:20px;font-weight:500}
.products-head h2 b{color:var(--orange);font-weight:500}
.products-head .arrows{font-size:24px;color:#444;letter-spacing:14px}
.product-row{display:flex;gap:24px;margin-top:26px}
.product{width:257px;position:relative}
.product-img{height:226px;border:1px solid var(--line);box-shadow:0 2px 6px rgba(0,0,0,.08);background:var(--white);display:flex;align-items:center;justify-content:center}
.product-img div{width:110px;height:150px;border-radius:20px;background:linear-gradient(160deg,#f4f6f8,#c9d2d9)}
.product h4{font-size:14px;font-weight:500;margin-top:18px}
.product .price{color:var(--orange);font-size:14px;margin-top:6px}
.cart{position:absolute;right:6px;top:252px;width:30px;height:30px;border-radius:50%;background:var(--blue);display:flex;align-items:center;justify-content:center}

.voices{height:228px;background:var(--light);text-align:center;padding-top:36px}
.voices h2{font-size:18px;font-weight:500;letter-spacing:.5px}
.voice-row{display:flex;justify-content:space-between;margin-top:30px;text-align:left}
.voice{display:flex;gap:16px;width:340px}
.avatar{width:78px;height:78px;border-radius:50%;flex:none;background:linear-gradient(160deg,#d7c5b5,#8a7566)}
.voice p{font-size:12px;line-height:1.55;color:var(--muted)}
.voice b{display:block;color:var(--blue);font-size:12px;font-weight:500;margin-top:8px}
.voice small{font-size:11px;color:var(--muted)}

.footer{height:284px;background:var(--orange);color:var(--white)}
.footer .wrap{display:flex;justify-content:space-between;padding-top:40px}
.col{width:240px}
.col h5{font-size:14px;font-weight:500;margin-bottom:16px;letter-spacing:.5px}
.col p,.col li{font-size:12px;line-height:1.8}
.col ul{list-style:none}
.newsletter{display:flex;margin-top:4px}
.newsletter span{flex:1;height:30px;background:var(--white)}
.newsletter em{font-style:normal;background:#333;font-size:12px;padding:0 12px;line-height:30px}
.social{display:flex;gap:8px;margin-top:16px}
.social i{width:26px;height:26px;border-radius:50%;background:rgba(255,255,255,.3);display:block}

.copyright{height:84px;background:#333;color:#bbb;font-size:12px;text-align:center;line-height:84px}
</style>
</head>
<body>

<div class="topbar"><div class="wrap">
  <span>Emergency Login</span>
  <nav><span>Login</span><span>Create an account</span><span>Country Flag</span></nav>
</div></div>

<header class="header"><div class="wrap">
  <div class="brand"><i></i>VitaBraid</div>
  <nav class="mainnav">
    <a class="active" href="#">HOME</a><a href="#">DISCOVER HEALTH VAULT</a><a href="#">SHOP</a><a href="#">CAREGIVE</a><a href="#">COMMUNITY</a>
  </nav>
</div></header>

<section class="hero">
  <div class="hero-photo" role="img" aria-label="Doctor with stethoscope working at a laptop in a bright clinic"></div>
  <div class="hero-text"><h1>Health Care</h1><p>Management system</p></div>
  <div class="hero-arrows">
    <span><svg width="10" height="10" viewBox="0 0 10 10"><path d="M7 1 3 5l4 4" stroke="#fff" stroke-width="2" fill="none"/></svg></span>
    <span><svg width="10" height="10" viewBox="0 0 10 10"><path d="M3 1l4 4-4 4" stroke="#fff" stroke-width="2" fill="none"/></svg></span>
  </div>
</section>

<section class="welcome">
  <h2>WELCOME TO <b>VITABRAID</b></h2>
  <p class="lead">Lorem Ipsum has been the industry's standard dummy text ever since the 1500s, when an unknown printer took a galley of type and scrambled it to make a type specimen book. It has survived not only five centuries, but also the leap into electronic typesetting, remaining essentially unchanged. It was popularised in the 1960s with the release of printed sample sheets containing Lorem Ipsum passages, and more recently with desktop publishing software.</p>
  <div class="cards">
    <div class="card">
      <div class="icon"><svg width="30" height="30" viewBox="0 0 30 30" fill="none" stroke="#fff" stroke-width="2"><circle cx="15" cy="15" r="12"/><path d="M3 15h24M15 3c5 5 5 19 0 24M15 3c-5 5-5 19 0 24"/></svg></div>
      <h3>OVERVIEW</h3>
      <p>Lorem Ipsum has been the industry's standard dummy text ever since the 1500s, when an unknown printer took a galley.</p>
    </div>
    <div class="card">
      <div class="icon"><svg width="30" height="30" viewBox="0 0 30 30"><path d="M3 14 27 4l-5 22-7-7-4 6v-8z" fill="#fff"/></svg></div>
      <h3>HOW IT WORKS</h3>
      <p>Lorem Ipsum has been the industry's standard dummy text ever since the 1500s, when an unknown printer took a galley.</p>
    </div>
    <div class="card">
      <div class="icon"><svg width="32" height="30" viewBox="0 0 32 30" fill="#fff"><circle cx="16" cy="9" r="5"/><path d="M7 25c0-6 4-9 9-9s9 3 9 9z"/><circle cx="6" cy="12" r="3.5"/><circle cx="26" cy="12" r="3.5"/></svg></div>
      <h3>ACCOUNTS</h3>
      <p>Lorem Ipsum has been the industry's standard dummy text ever since the 1500s, when an unknown printer took a galley.</p>
    </div>
    <div class="card">
      <div class="icon"><svg width="30" height="30" viewBox="0 0 30 30" fill="none" stroke="#fff" stroke-width="3"><circle cx="11" cy="12" r="6"/><circle cx="22" cy="22" r="4"/></svg></div>
      <h3>GET STARTED</h3>
      <p>Lorem Ipsum has been the industry's standard dummy text ever since the 1500s, when an unknown printer took a galley.</p>
    </div>
  </div>
</section>

<section class="system"><div class="wrap">
  <div class="system-photo" role="img" aria-label="Clinician reviewing patient records on a tablet"></div>
  <div class="system-copy">
    <h2>HEALTH CARE MANAGEMENT SYSTEM</h2>
    <p>Lorem Ipsum has been the industry's standard dummy text ever since the 1500s, when an unknown printer took a galley of type and scrambled it to make a type specimen book. It has survived not only five centuries, but also the leap into electronic typesetting, remaining essentially unchanged. It was popularised in the 1960s with the release of printed sample sheets containing Lorem Ipsum passages, and more recently with desktop publishing software including versions of Lorem Ipsum.</p>
    <span class="btn">Read More</span>
  </div>
</div></section>

<section class="products"><div class="wrap">
  <div class="products-head"><h2>FEATURE <b>PRODUCTS</b></h2><span class="arrows">‹›</span></div>
  <div class="product-row">
    <div class="product"><div class="product-img" role="img" aria-label="Wearable health monitor"><div></div></div><h4>PRODUCT NAME</h4><div class="price">$ 91.00</div><span class="cart"><svg width="14" height="14" viewBox="0 0 14 14" fill="#fff"><path d="M1 2h2l2 7h7l1-5H4"/><circle cx="6" cy="12" r="1.3"/><circle cx="11" cy="12" r="1.3"/></svg></span></div>
    <div class="product"><div class="product-img" role="img" aria-label="Blood pressure cuff"><div></div></div><h4>PRODUCT NAME</h4><div class="price">$ 91.00</div><span class="cart"><svg width="14" height="14" viewBox="0 0 14 14" fill="#fff"><path d="M1 2h2l2 7h7l1-5H4"/><circle cx="6" cy="12" r="1.3"/><circle cx="11" cy="12" r="1.3"/></svg></span></div>
    <div class="product"><div class="product-img" role="img" aria-label="Fitness tracker wristband"><div></div></div><h4>PRODUCT NAME</h4><div class="price">$ 91.00</div><span class="cart"><svg width="14" height="14" viewBox="0 0 14 14" fill="#fff"><path d="M1 2h2l2 7h7l1-5H4"/><circle cx="6" cy="12" r="1.3"/><circle cx="11" cy="12" r="1.3"/></svg></span></div>
    <div class="product"><div class="product-img" role="img" aria-label="Fingertip pulse oximeter"><div></div></div><h4>PRODUCT NAME</h4><div class="price">$ 91.00</div><span class="cart"><svg width="14" height="14" viewBox="0 0 14 14" fill="#fff"><path d="M1 2h2l2 7h7l1-5H4"/><circle cx="6" cy="12" r="1.3"/><circle cx="11" cy="12" r="1.3"/></svg></span></div>
  </div>
</div></section>

<section class="voices"><div class="wrap">
  <h2>FIND OUT WAY PEOPLE ARE USING VITABRAID HEALTH VAULT</h2>
  <div class="voice-row">
    <div class="voice"><div class="avatar" role="img" aria-label="Portrait of a customer"></div><div><p>“Lorem Ipsum is simply dummy text of the printing and typesetting industry.”</p><b>MARA ELLISON</b><small>Marketing Executive</small></div></div>
    <div class="voice"><div class="avatar" role="img" aria-label="Portrait of a customer"></div><div><p>“Lorem Ipsum is simply dummy text of the printing and typesetting industry.”</p><b>MARA ELLISON</b><small>Marketing Executive</small></div></div>
    <div class="voice"><div class="avatar" role="img" aria-label="Portrait of a customer"></div><div><p>“Lorem Ipsum is simply dummy text of the printing and typesetting industry.”</p><b>MARA ELLISON</b><small>Marketing Executive</small></div></div>
  </div>
</div></section>

<footer class="footer"><div class="wrap">
  <div class="col"><h5>TEXT WIDGET</h5><p>Aliquam erat in purus sit amet mollis. Nulla facilisi, sed tempor ligula varius. Quisque nec elit vel lorem dapibus consequat nec at nisi. Donec sed mauris at urna.</p></div>
  <div class="col"><h5>LINKS</h5><ul><li>› Individual Users</li><li>› Small Business</li><li>› Health Vault</li><li>› Online Shop</li><li>› Community</li></ul></div>
  <div class="col"><h5>GET IN TOUCH</h5><p>Address: 42 Meadow Row, Suite 7</p><p>Brookfield, ST 00000</p><p>Phone: +1 (555) 010-2040</p><p>Email: hello@vitabraid.example</p></div>
  <div class="col"><h5>NEWSLETTER</h5><div class="newsletter"><span></span><em>Submit</em></div><div class="social"><i></i><i></i><i></i><i></i></div></div>
</div></footer>

<div class="copyright">Copyright © 2015, All Rights Reserved</div>

</body>
</html>
```